Upscale and cool gun range / bar + lounge. Think axe throwing, but much cooler.

capture interest and make them want to know more.

s/b more on the cool and hip side to be on brand

will be offering a gift card. example attached

```html
<!DOCTYPE html>
<html lang="en">
<head>
<meta charset="utf-8">
<title>Farmark Airgun Range + Social Club</title>
<link rel="stylesheet" href="https://fonts.googleapis.com/css2?family=Montserrat:wght@400;500&family=Roboto+Condensed:wght@300;400;700&display=swap">
<style>
  :root {
    --paper: #ffffff;
    --ink: #000000;
    --text: #ffffff;
    --accent: #f5a623;
  }
  * { margin: 0; padding: 0; box-sizing: border-box; }
  html, body { width: 1200px; height: 1008px; overflow: hidden; background: var(--paper); }
  .card { position: relative; width: 1200px; height: 1008px; background: var(--paper); }
  .card__art { position: absolute; inset: 0; }
  .intro {
    position: absolute; left: 269px; top: 268px; width: 490px;
    font-family: "Montserrat", sans-serif; font-weight: 400;
    font-size: 19.5px; line-height: 28.6px; color: var(--text);
  }
  .pricing {
    position: absolute; left: 269px; top: 438px;
    font-family: "Roboto Condensed", sans-serif; color: var(--text);
  }
  .pricing__heading {
    font-weight: 700; font-size: 24px; line-height: 30px;
    color: var(--accent); margin-bottom: 13px; letter-spacing: 0.2px;
  }
  .package__name { font-weight: 700; font-size: 25px; line-height: 27.4px; }
  .package__detail { font-weight: 300; font-size: 19px; line-height: 27.4px; letter-spacing: 0.2px; }
  .brand {
    position: absolute; left: 929px; top: 543px; width: 240px;
    text-align: center; font-family: "Roboto Condensed", sans-serif; color: var(--text);
  }
  .brand__mark {
    display: block; margin: 0 auto 24px; width: 94px; height: 94px;
    border: 3px solid var(--text); border-radius: 50%;
  }
  .brand__name {
    font-weight: 700; font-size: 19px; letter-spacing: 5px; line-height: 24px;
    margin-bottom: 18px;
  }
  .brand__tagline { font-weight: 700; font-size: 21px; line-height: 27px; }
</style>
</head>
<body>
<main class="card">
  <svg class="card__art" width="1200" height="1008" viewBox="0 0 1200 1008">
    <rect class="panel" x="167" y="200" width="1002" height="787" rx="20" fill="var(--ink)"/>
    <rect class="mascot" role="img" aria-label="Black silhouette of a cat holding a pistol" x="30" y="40" width="570" height="947" rx="40" fill="var(--ink)"/>
  </svg>

  <p class="intro">As the only Airgun Shooting Range + Social Club in North America, we can offer you an adrenaline rush that few other activities can compare to.</p>

  <section class="pricing">
    <h2 class="pricing__heading">PRICING</h2>
    <div class="package__name">THE AGENT | $59.99</div>
    <div class="package__detail">30 MINS - RIFLE OR PISTOL - UNLIMITED ROUNDS</div>
    <div class="package__name">THE COMMANDO | $109.00</div>
    <div class="package__detail">60 MINS - RIFLE OR PISTOL - UNLIMITED ROUNDS</div>
    <div class="package__name">THE RANCHER| $139.00</div>
    <div class="package__detail">60 MINS - RIFLE OR PISTOL - UNLIMITED ROUNDS</div>
    <div class="package__detail">AIR JAVELIN: 6 ARROWS</div>
    <div class="package__name">THE BIG GAME HUNTER| $25.00</div>
    <div class="package__detail">AIR JAVELIN - 10 ARROWS</div>
    <div class="package__name">THE ARMORER| $40</div>
    <div class="package__detail">30 MINS - RIFLE OR PISTOL - UNLIMITED ROUNDS</div>
  </section>

  <aside class="brand">
    <span class="brand__mark"></span>
    <div class="brand__name">FARMARK</div>
    <div class="brand__tagline">SHOOT GUNS*.<br>SHOOT DRINKS.</div>
  </aside>
</main>
</body>
</html>
```